Indy Film Production Company/Studio

We need a business card designed from an existing logo. We are a digital studio/production company that caters to creating genre entertainment, like Action, Horror, and martial arts. The card along with the logo will be used to Brand the company from letter heads to banners. The design will also be used for postcards and Brochures. It should be professional and masculine.
Updates

Thank you to all the designers who have participated. I'm narrowing down who it will be. Thank you again.

Target Market(s)

Investors, Networks, Producers, and actors

Industry/Entity Type

Film Production

Contact Information for Business Card

Teodoro Valbuena
Producer/Writer/Director
www.kestrelpicturehouse.example

Requirements
Must have
• Website address, Facebook icon and Twitter icon possibly in the back of the card.
Nice to have
• Logline of Company: Follow The Action.

```html
<!DOCTYPE html>
<html lang="en">
<head>
<meta charset="utf-8">
<title>Kestrel Picture House – Business Card</title>
<link rel="stylesheet" href="https://fonts.googleapis.com/css2?family=Open+Sans:wght@400;600;800&display=swap">
<style>
  :root {
    --brand-red: #ec1c24;
    --paper-white: #ffffff;
    --ink-dark: #1f1f1f;
    --backdrop: #e9e6e1;
    --card-shadow: rgba(0, 0, 0, 0.22);
  }
  * { box-sizing: border-box; margin: 0; padding: 0; }
  html, body {
    width: 1200px;
    height: 900px;
    overflow: hidden;
    background: var(--backdrop);
    font-family: "Open Sans", Arial, sans-serif;
  }
  .stage {
    position: relative;
    width: 1200px;
    height: 900px;
  }
  .card {
    position: absolute;
    width: 600px;
    height: 343px;
    box-shadow: 0 10px 28px var(--card-shadow);
  }
  .card--front {
    left: 90px;
    top: 100px;
    background: var(--brand-red);
  }
  .card--back {
    left: 510px;
    top: 450px;
    background: var(--paper-white);
  }
  .wordmark {
    position: absolute;
    display: flex;
    align-items: center;
    gap: 12px;
    font-weight: 800;
    letter-spacing: 1px;
    text-transform: uppercase;
    line-height: 1.05;
  }
  .wordmark__square {
    width: 18px;
    height: 18px;
    flex: none;
  }
  .card--front .wordmark {
    left: 150px;
    top: 128px;
    color: var(--paper-white);
    font-size: 30px;
  }
  .card--front .wordmark__square { background: var(--paper-white); }
  .card--back .wordmark {
    left: 128px;
    top: 244px;
    color: var(--brand-red);
    font-size: 26px;
  }
  .card--back .wordmark__square { background: var(--brand-red); }

  .contact {
    position: absolute;
    left: 330px;
    top: 32px;
    color: var(--ink-dark);
    font-size: 13px;
    line-height: 1.35;
  }
  .contact__name {
    color: var(--brand-red);
    font-weight: 600;
    font-size: 19px;
    line-height: 1.2;
  }
  .contact__role { margin-bottom: 12px; }
  .contact__address { margin-bottom: 10px; }
  .contact__list { list-style: none; }
  .contact__item {
    display: flex;
    align-items: center;
    gap: 10px;
    margin-bottom: 2px;
  }
  .contact__icon {
    width: 11px;
    height: 11px;
    flex: none;
    fill: var(--brand-red);
    stroke: var(--brand-red);
  }
  .social {
    display: flex;
    gap: 8px;
    margin-top: 8px;
  }
  .social__badge {
    width: 16px;
    height: 16px;
    border-radius: 50%;
    background: var(--brand-red);
  }
</style>
</head>
<body>
<main class="stage">
  <section class="card card--front" aria-label="Card front">
    <div class="wordmark">
      <span class="wordmark__square"></span>
      <span>Kestrel<br>Picture House</span>
    </div>
  </section>

  <section class="card card--back" aria-label="Card back">
    <div class="contact">
      <p class="contact__name">Teodoro Valbuena</p>
      <p class="contact__role">Producer/Writer/Director</p>
      <p class="contact__address">12345, Address Goes Here<br>Country Name, 123456.</p>
      <ul class="contact__list">
        <li class="contact__item">
          <svg class="contact__icon" viewBox="0 0 12 12" aria-hidden="true"><path stroke="none" d="M2.4 0.8 4.2 2.9 3.3 4.3c.7 1.6 2.2 3.2 4.4 4.4l1.4-.9 2.1 1.8-1.2 1.6C5.4 11.6.4 6.6.8 2z"/></svg>
          <span>044-555 010 234</span>
        </li>
        <li class="contact__item">
          <svg class="contact__icon" viewBox="0 0 12 12" aria-hidden="true"><rect x="0.5" y="2" width="11" height="8" stroke="none"/><path d="M0.8 2.5 6 6.6 11.2 2.5" fill="none" stroke="#fff" stroke-width="1"/></svg>
          <span>info@kestrelpicturehouse.example</span>
        </li>
        <li class="contact__item">
          <svg class="contact__icon" viewBox="0 0 12 12" aria-hidden="true"><g fill="none" stroke-width="1.6" stroke-linecap="round"><path d="M5 7 7 5"/><path d="M4.2 5.4 2.6 7a1.7 1.7 0 0 0 2.4 2.4l1.6-1.6"/><path d="M7.8 6.6 9.4 5A1.7 1.7 0 0 0 7 2.6L5.4 4.2"/></g></svg>
          <span>www.kestrelpicturehouse.example</span>
        </li>
      </ul>
      <div class="social">
        <span class="social__badge" role="img" aria-label="Social profile one"></span>
        <span class="social__badge" role="img" aria-label="Social profile two"></span>
      </div>
    </div>
    <div class="wordmark">
      <span class="wordmark__square"></span>
      <span>Kestrel<br>Picture House</span>
    </div>
  </section>
</main>
</body>
</html>
```